goal design

We are rolling out a goal for the next 3 years. the goal is as follows:
2014: $8 million gross profit, $1.25 million net income
2015: $12 million gross profit, $2.4 million net income
2016 $15 million gross profit, $4 million net income
We want a design that captures these numbers and that we can publish company wide that will quickly remind everyone of these goals. Our website is www.brackenfieldcrew.com. This will be an internal campaign. We will use the simple design to remind our people of our goals for the next 3 years. We will print it on mouse pads, shirts and things of this nature periodically to keep it front of mind for our people. So easy to remember, visually appealing and simple are good guidelines.
Updates
Target Market(s)
This is an internal campaign. it is to remind our people of our goals for the next few years so will be on little reminder items (i.e. cell phone covers, mouse pads, shirts, screen savers, etc).
Industry/Entity Type
It Company
Look and feel

```html
<!DOCTYPE html>
<html lang="en">
<head>
<meta charset="utf-8">
<title>Just Achieve it – Three-Year Goals</title>
<link rel="stylesheet" href="https://fonts.googleapis.com/css2?family=Arimo:wght@700&family=Roboto+Condensed:wght@700&display=swap">
<style>
  :root {
    --brand-blue: #2e86c8;
    --ink: #000000;
    --paper: #ffffff;
  }
  html, body {
    margin: 0;
    padding: 0;
    width: 1200px;
    height: 1000px;
    overflow: hidden;
    background: var(--paper);
  }
  .goal-poster {
    display: block;
    width: 1200px;
    height: 1000px;
  }
  .arch { fill: var(--ink); }
  .arch-label {
    fill: var(--paper);
    font-family: "Arimo", Arial, sans-serif;
    font-weight: 700;
    font-size: 22px;
    letter-spacing: 1px;
  }
  .gross-figure {
    fill: var(--brand-blue);
    font-family: "Arimo", Arial, sans-serif;
    font-weight: 700;
    font-size: 50px;
  }
  .net-label {
    fill: var(--ink);
    font-family: "Roboto Condensed", "Arial Narrow", sans-serif;
    font-weight: 700;
    font-size: 22px;
  }
  .net-figure {
    fill: var(--ink);
    font-family: "Roboto Condensed", "Arial Narrow", sans-serif;
    font-weight: 700;
    font-size: 44px;
  }
  .year {
    fill: var(--brand-blue);
    font-family: "Arimo", Arial, sans-serif;
    font-weight: 700;
    font-size: 54px;
  }
  .baseline-rule { stroke: var(--ink); stroke-width: 5; }
  .slogan {
    fill: var(--brand-blue);
    font-family: "Arimo", Arial, sans-serif;
    font-weight: 700;
    font-size: 100px;
  }
</style>
</head>
<body>
<svg class="goal-poster" viewBox="0 0 900 750" xmlns="http://www.w3.org/2000/svg" aria-label="Three-year goals: 2014, 2015 and 2016 gross profit and net income">
  <defs>
    <path id="label-path-2014" d="M45,470 C50,370 110,339 162,339 C215,339 275,370 280,470"/>
    <path id="label-path-2015" d="M330,470 C335,262 390,206 445,206 C500,206 555,262 560,470"/>
    <path id="label-path-2016" d="M612,470 C615,200 670,149 730,149 C790,149 845,200 848,470"/>
  </defs>

  <!-- 2014 -->
  <g class="goal goal-2014" text-anchor="middle">
    <path class="arch" d="M20,545 C20,380 90,313 162,313 C235,313 305,380 305,545 C290,420 235,365 162,365 C90,365 35,420 20,545 Z"/>
    <text class="arch-label" dominant-baseline="middle"><textPath href="#label-path-2014" startOffset="50%">Gross Profit</textPath></text>
    <text class="gross-figure" x="160" y="300">$8 m</text>
    <text class="net-label" x="160" y="422">Net Income</text>
    <text class="net-figure" x="160" y="478">$1.25 m</text>
    <text class="year" x="160" y="565">2014</text>
  </g>

  <!-- 2015 -->
  <g class="goal goal-2015" text-anchor="middle">
    <path class="arch" d="M300,545 C300,300 370,172 445,172 C520,172 585,300 585,545 C570,330 515,240 445,240 C375,240 315,330 300,545 Z"/>
    <text class="arch-label" dominant-baseline="middle"><textPath href="#label-path-2015" startOffset="50%">Gross Profit</textPath></text>
    <text class="gross-figure" x="445" y="160">$12 m</text>
    <text class="net-label" x="445" y="303">Net Income</text>
    <text class="net-figure" x="445" y="360">$2.4 m</text>
    <text class="year" x="445" y="565">2015</text>
  </g>

  <!-- 2016 -->
  <g class="goal goal-2016" text-anchor="middle">
    <path class="arch" d="M585,545 C585,250 660,113 730,113 C800,113 880,250 880,545 C865,300 800,185 730,185 C660,185 600,300 585,545 Z"/>
    <text class="arch-label" dominant-baseline="middle"><textPath href="#label-path-2016" startOffset="50%">Gross Profit</textPath></text>
    <text class="gross-figure" x="728" y="100">$15 m</text>
    <text class="net-label" x="728" y="237">Net Income</text>
    <text class="net-figure" x="728" y="288">$4 m</text>
    <text class="year" x="728" y="565">2016</text>
  </g>

  <line class="baseline-rule" x1="18" y1="582" x2="878" y2="582"/>
  <text class="slogan" x="22" y="680" textLength="856" lengthAdjust="spacingAndGlyphs">Just Achieve it !</text>
</svg>
</body>
</html>
```